Brightlane Rapid Rinse Web Design

We are looking for a web design that highlights our state of the art fully automated commercial vehicle washing equipment. Similar system to a car wash however this system is meant for the largest vehicles on our roadways. Transport trucks with or without a trailer, busses both highway and school, RV's from 5th wheel type to A Class. Cement trucks, dump trucks, vac trucks, fuel trucks etc. Pick ups with utility trailers...Refrigerator truck clean outs.
Brightlane Rapid Rinse will wash your vehicle quickly and with a minimal impact on the environment

Home page
About us
Why Brightlane
Services and pricing
Videos of wash system
Fleets
contact us

Target Market(s)

Commercial vehicle owners and operators as well as corporate fleets. Includes busses, municipal, school and highway.both school and

Industry/Entity Type

transportation

Coding

Coded - Design and coding required

Number of Pages Required

5+ page

Font styles to use
Sans Serif

Colors
0054AA
0677BA
7BADD7
CADEEF
E8F1F8

Requirements
Must have
• Welcome page,why us page which describes the financial and environmental benefits. payment processing page, contact us page, Services which is washing vehicles and greasing for commercial vehicles that want that service and grease
Nice to have
• pictures of both clean and dirty commercial vehicles ie. before and after

```html
<!DOCTYPE html>
<html lang="en">
<head>
<meta charset="utf-8">
<title>Brightlane Rapid Rinse</title>
<link href="https://fonts.googleapis.com/css2?family=Montserrat:wght@600;700;800&family=Roboto:ital,wght@0,400;0,500;0,700;1,400&display=swap" rel="stylesheet">
<style>
:root{
  --blue:#0054AA;
  --blue-mid:#0677BA;
  --blue-soft:#7BADD7;
  --blue-pale:#CADEEF;
  --blue-mist:#E8F1F8;
  --ink:#111;
  --grey:#666;
  --white:#fff;
}
*{margin:0;padding:0;box-sizing:border-box}
html,body{width:1200px;height:4141px;overflow:hidden}
body{position:relative;background:var(--white);font-family:'Roboto',Arial,sans-serif;color:var(--ink)}
.abs{position:absolute}
.heading{font-family:'Montserrat',Arial,sans-serif;font-weight:700;text-transform:uppercase;color:var(--ink)}
.section-title{position:absolute;left:0;width:1200px;text-align:center;font-size:40px}
.rule{position:absolute;height:4px;width:64px;background:var(--blue);left:568px}
.btn{position:absolute;display:flex;align-items:center;justify-content:center;gap:6px;border-radius:30px;background:var(--blue);color:var(--white);font-family:'Roboto',Arial,sans-serif;font-weight:700;font-size:13.5px;text-transform:uppercase}
.btn.light{background:var(--white);color:var(--ink)}
.btn svg{width:13px;height:13px}
.photo{position:absolute}

/* hero */
.hero{left:0;top:0;width:1200px;height:723px;background:linear-gradient(100deg,#3a3d42 0%,#6b6f74 45%,#8e9297 70%,#4f5358 100%)}
.hero-shade{left:0;top:0;width:1200px;height:723px;background:linear-gradient(90deg,rgba(0,0,0,.55) 0%,rgba(0,0,0,.25) 55%,rgba(0,0,0,0) 100%)}
.brand{font-family:'Montserrat',Arial,sans-serif;font-weight:700;color:var(--white);text-transform:uppercase;line-height:1.1}
.nav{left:326px;top:36px;display:flex;gap:29px;color:var(--white);font-size:14px}
.nav span.on{position:relative}
.nav span.on:before{content:"";position:absolute;left:0;top:-19px;width:40px;height:2px;background:var(--blue-soft)}
.callbox{left:915px;top:0;width:285px;height:92px;background:var(--blue);clip-path:polygon(8% 0,100% 0,100% 100%,0 100%);color:var(--white)}
.callbox .ring{position:absolute;left:51px;top:30px;width:34px;height:34px;border-radius:50%;background:var(--white);display:flex;align-items:center;justify-content:center}
.hero-title{left:111px;top:246px;font-size:55px;line-height:60px;color:var(--white)}
.hero-tag{left:116px;top:374px;padding:0 8px;background:var(--white);color:var(--blue-mid);font-family:'Montserrat',Arial,sans-serif;font-weight:700;font-size:37px;line-height:46px}
.hero-copy{left:111px;top:436px;width:560px;color:var(--white);font-size:13.5px;line-height:21px}
.slide-arrow{position:absolute;width:42px;height:42px;border-radius:50%;background:var(--white);display:flex;align-items:center;justify-content:center}

/* about */
.badge{left:174px;top:868px;width:118px;height:118px;border-radius:50%;background:var(--blue);border:4px solid var(--white);color:var(--white);text-align:center;padding-top:22px}
.body-copy{font-size:13.5px;line-height:26px;color:var(--grey);text-align:justify}

/* services */
.service{position:absolute;top:1469px;width:434px;height:434px;border-radius:50%;background:var(--white);border:19px solid var(--blue-soft);text-align:center}
.service.main{border-color:var(--blue)}
.service .icon{position:absolute;left:155px;top:48px;width:86px;height:86px;border-radius:50%;background:var(--blue);display:flex;align-items:center;justify-content:center}
.service h3{position:absolute;left:0;width:396px;top:163px;font-family:'Roboto',Arial,sans-serif;font-weight:500;font-size:21px;text-transform:uppercase}
.service p{position:absolute;left:43px;width:310px;top:202px;font-size:13.5px;line-height:26px;color:var(--grey)}
.service .btn{left:116px;top:290px;width:164px;height:48px}

/* testimonial */
.card{left:111px;top:2668px;width:488px;height:265px;background:var(--white)}

/* faq */
.faq{position:absolute;left:259px;width:681px;height:55px;border-radius:28px;background:var(--white);box-shadow:0 3px 10px rgba(0,0,0,.12);display:flex;align-items:center;padding-left:39px;font-size:13.5px;color:var(--grey)}
.faq .plus{position:absolute;right:14px;top:10px;width:35px;height:35px;border-radius:50%;background:var(--blue);color:var(--white);display:flex;align-items:center;justify-content:center;font-size:18px}

/* footer */
.footer{left:0;top:3712px;width:1200px;height:429px;background:linear-gradient(180deg,#0a5fba 0%,var(--blue) 60%,#004a97 100%)}
.foot-head{font-family:'Montserrat',Arial,sans-serif;font-weight:700;font-size:16px;color:var(--white);text-transform:uppercase}
.foot-list{color:var(--white);font-size:13px;line-height:27.5px}
.social{position:absolute;top:3875px;width:32px;height:32px;border-radius:50%;border:1.5px solid var(--white)}
.contact-label{font-weight:700;font-size:12px;color:var(--white)}
.contact-val{font-size:13.5px;color:var(--white);line-height:18px}
</style>
</head>
<body>

<!-- HERO -->
<div class="abs hero" role="img" aria-label="Photo of a white truck cab inside an automated wash bay"></div>
<div class="abs hero-shade"></div>
<div class="abs brand" style="left:111px;top:28px;font-size:17px">Brightlane<br><span style="color:var(--blue-soft);font-size:10px;letter-spacing:5px;font-weight:600">Rapid Rinse</span></div>
<nav class="abs nav"><span class="on">Home</span><span>About Us</span><span>Why Brightlane</span><span>Services and pricing</span><span>Contact</span><span>More</span></nav>
<div class="abs callbox">
  <div class="ring"><svg width="17" height="17" viewBox="0 0 24 24"><path fill="#0054AA" d="M6.6 10.8a15 15 0 0 0 6.6 6.6l2.2-2.2c.3-.3.7-.4 1-.2 1.1.4 2.3.6 3.6.6.6 0 1 .4 1 1V20c0 .6-.4 1-1 1A17 17 0 0 1 3 4c0-.6.4-1 1-1h3.5c.6 0 1 .4 1 1 0 1.3.2 2.5.6 3.6.1.3 0 .7-.2 1z"/></svg></div>
  <div class="abs" style="left:98px;top:27px;font-size:13.5px">Call Us Today :</div>
  <div class="abs" style="left:98px;top:42px;font-size:21px;font-weight:700">+1 888 888 8888</div>
</div>
<h1 class="abs heading hero-title">Brightlane<br>Rapid Rinse</h1>
<div class="abs hero-tag">(LESS THAN 15 MINUTES)</div>
<p class="abs hero-copy">A concise statement about our dedication to revolutionizing truck washing with advanced technology and sustainable practices, set against a dark blue backdrop.</p>
<div class="btn" style="left:111px;top:495px;width:162px;height:48px">Book a Wash</div>
<div class="btn light" style="left:283px;top:495px;width:162px;height:48px">Learn More</div>
<div class="btn" style="left:453px;top:495px;width:164px;height:48px">Contact Us</div>
<div class="slide-arrow" style="left:991px;top:633px"><svg width="14" height="14" viewBox="0 0 24 24"><path d="M15 4 7 12l8 8" fill="none" stroke="#222" stroke-width="3"/></svg></div>
<div class="slide-arrow" style="left:1044px;top:633px"><svg width="14" height="14" viewBox="0 0 24 24"><path d="m9 4 8 8-8 8" fill="none" stroke="#222" stroke-width="3"/></svg></div>

<!-- ABOUT -->
<div class="photo" style="left:235px;top:830px;width:528px;height:375px;background:linear-gradient(135deg,#2a4a66 0%,#3f8fc0 45%,#b5d7ea 75%,#1d3a52 100%)" role="img" aria-label="Close-up of robotic wash brushes spraying water"></div>
<div class="abs" style="left:620px;top:911px;width:580px;height:400px;background:var(--white)"></div>
<div class="photo" style="left:113px;top:1018px;width:325px;height:267px;border:4px solid var(--white);background:linear-gradient(180deg,#8aa4b8 0%,#5f7d96 50%,#c7d6e0 100%)" role="img" aria-label="Car passing through a tunnel wash with blue brushes"></div>
<div class="abs badge"><div style="font-size:26px;font-weight:700;line-height:28px">25</div><div style="font-size:13.5px;line-height:17px">Years<br>Experience</div></div>
<h2 class="abs heading" style="left:647px;top:932px;font-size:38px">About Us</h2>
<div class="abs" style="left:647px;top:992px;width:66px;height:4px;background:var(--blue)"></div>
<p class="abs body-copy" style="left:647px;top:1010px;width:441px">Lorem ipsum dolor sit amet, consectetur adipiscing elit, sed do eiusmod tempor incididunt ut labore et dolore magna aliqua. Ut enim ad minim veniam, quis nostrud exercitation ullamco laboris nisi ut aliquip ex ea commodo consequat.</p>
<p class="abs body-copy" style="left:647px;top:1138px;width:441px">Duis aute irure dolor in reprehenderit in voluptate velit esse cillum dolore eu fugiat nulla pariatur.Lorem ipsum dolor sit amet, consec tetur adipiscing elit, sed do eiusmod tempor incididunt</p>
<div class="btn" style="left:647px;top:1237px;width:164px;height:48px">Learn More <svg viewBox="0 0 24 24"><circle cx="12" cy="12" r="11" fill="#fff"/><path d="m10 7 5 5-5 5" fill="none" stroke="#0054AA" stroke-width="3"/></svg></div>

<!-- SERVICES -->
<h2 class="heading section-title" style="top:1376px">Our Services</h2>
<div class="rule" style="top:1436px"></div>

<div class="service" style="left:-18px">
  <div class="icon"><svg width="48" height="48" viewBox="0 0 48 48" fill="none" stroke="#fff" stroke-width="2"><rect x="6" y="12" width="22" height="18"/><path d="M28 18h8l6 7v5H28z"/><circle cx="13" cy="33" r="3"/><circle cx="35" cy="33" r="3"/><path d="m12 21 4 4 7-7"/></svg></div>
  <h3>Automated Truck Wash</h3>
  <p>Lorem ipsum dolor sit amet, consectetur adipi scing elit, sed do eiusmod tempor incididunt ut labore et dolore magna aliqua.</p>
  <div class="btn">Learn More <svg viewBox="0 0 24 24"><circle cx="12" cy="12" r="11" fill="#fff"/><path d="m10 7 5 5-5 5" fill="none" stroke="#0054AA" stroke-width="3"/></svg></div>
</div>
<div class="service main" style="left:383px">
  <div class="icon"><svg width="48" height="48" viewBox="0 0 48 48" fill="none" stroke="#fff" stroke-width="2"><rect x="9" y="10" width="12" height="28" rx="2"/><rect x="27" y="10" width="12" height="28" rx="2"/><path d="M12 16h6M12 22h6M30 16h6M30 22h6M15 38v4M33 38v4"/></svg></div>
  <h3>Additional Services</h3>
  <p>Lorem ipsum dolor sit amet, consectetur adipi scing elit, sed do eiusmod tempor incididunt ut labore et dolore magna aliqua.</p>
  <div class="btn">Learn More <svg viewBox="0 0 24 24"><circle cx="12" cy="12" r="11" fill="#fff"/><path d="m10 7 5 5-5 5" fill="none" stroke="#0054AA" stroke-width="3"/></svg></div>
</div>
<div class="service" style="left:784px">
  <div class="icon"><svg width="48" height="48" viewBox="0 0 48 48" fill="none" stroke="#fff" stroke-width="2"><rect x="8" y="8" width="16" height="12" rx="2"/><rect x="24" y="22" width="16" height="12" rx="2"/><rect x="8" y="28" width="12" height="10" rx="2"/><circle cx="12" cy="40" r="2"/><circle cx="36" cy="36" r="2"/></svg></div>
  <h3>Fleet Services</h3>
  <p>Lorem ipsum dolor sit amet, consectetur adipi scing elit, sed do eiusmod tempor incididunt ut labore et dolore magna aliqua.</p>
  <div class="btn">Learn More <svg viewBox="0 0 24 24"><circle cx="12" cy="12" r="11" fill="#fff"/><path d="m10 7 5 5-5 5" fill="none" stroke="#0054AA" stroke-width="3"/></svg></div>
</div>

<!-- PROJECTS -->
<h2 class="heading section-title" style="top:1996px">Our Projects</h2>
<div class="rule" style="top:2056px"></div>
<div class="photo" style="left:111px;top:2088px;width:241px;height:305px;background:linear-gradient(180deg,#5f97cf 0%,#a9c9e4 45%,#8a7a6a 100%)" role="img" aria-label="Trailer truck on a desert road under blue sky"></div>
<div class="photo" style="left:352px;top:2088px;width:241px;height:305px;background:linear-gradient(180deg,#c98d4c 0%,#e8b97a 40%,#3c4a5e 100%)" role="img" aria-label="Blue semi truck at sunset"></div>
<div class="photo" style="left:605px;top:2088px;width:241px;height:305px;background:linear-gradient(180deg,#8fa6b8 0%,#b9a27d 50%,#4b4a48 100%)" role="img" aria-label="Cargo truck on a highway in warm light"></div>
<div class="photo" style="left:846px;top:2088px;width:241px;height:305px;background:linear-gradient(180deg,#6da3d6 0%,#cfe0ee 45%,#5b5f64 100%)" role="img" aria-label="White truck with trailer on an open road"></div>
<svg class="abs" style="left:43px;top:2230px" width="20" height="26" viewBox="0 0 20 26"><path d="M15 2 4 13l11 11" fill="none" stroke="#222" stroke-width="2.5"/></svg>
<svg class="abs" style="left:1132px;top:2230px" width="20" height="26" viewBox="0 0 20 26"><path d="m5 2 11 11L5 24" fill="none" stroke="#222" stroke-width="2.5"/></svg>

<!-- TESTIMONIAL -->
<div class="abs" style="left:0;top:2570px;width:1200px;height:321px;background:var(--blue)"></div>
<div class="photo" style="left:519px;top:2517px;width:568px;height:416px;background:linear-gradient(135deg,#cfd3d6 0%,#9aa1a7 35%,#b8363a 55%,#8ba6c1 80%,#e9eaeb 100%)" role="img" aria-label="Red truck on an assembly line with yellow robots"></div>
<div class="abs card">
  <h2 class="abs heading" style="left:30px;top:34px;font-size:29px;white-space:nowrap">What Our Clients Say</h2>
  <div class="abs" style="left:30px;top:87px;width:30px;height:2px;background:var(--blue-soft)"></div>
  <p class="abs body-copy" style="left:35px;top:100px;width:420px;font-style:italic">"Lorem ipsum dolor sit amet, consectetur adipiscing elit, sed do eiusmod tempor incididunt ut labore et dolore magna aliqua. Ut enim ad minim veniam, quis nostrud exercitation ullamco laboris nisi ut aliquip ex ea commodo consequat. "</p>
  <div class="abs" style="left:37px;top:216px;font-size:18px;font-weight:500;color:#333">John Doe</div>
  <div class="abs" style="left:37px;top:248px;font-size:13.5px;color:var(--grey)">Company name</div>
  <svg class="abs" style="left:364px;top:236px" width="34" height="20" viewBox="0 0 34 20"><path d="M32 10H3M11 2 3 10l8 8" fill="none" stroke="#aaa" stroke-width="2.5"/></svg>
  <svg class="abs" style="left:407px;top:236px" width="34" height="20" viewBox="0 0 34 20"><path d="M2 10h29M23 2l8 8-8 8" fill="none" stroke="#0054AA" stroke-width="2.5"/></svg>
</div>

<!-- FAQ -->
<h2 class="heading section-title" style="top:3066px">Frequently Asked Questions</h2>
<div class="rule" style="top:3126px"></div>
<div class="faq" style="top:3183px">Lorem ipsum dolor sit amet, consectetur adipiscing elit, sed<span class="plus">+</span></div>
<div class="faq" style="top:3252px">Lorem ipsum dolor sit amet, consectetur adipiscing elit, sed<span class="plus">+</span></div>
<div class="faq" style="top:3321px">Lorem ipsum dolor sit amet, consectetur adipiscing elit, sed<span class="plus">+</span></div>
<div class="faq" style="top:3389px">Lorem ipsum dolor sit amet, consectetur adipiscing elit, sed<span class="plus">+</span></div>
<div class="faq" style="top:3458px">Lorem ipsum dolor sit amet, consectetur adipiscing elit, sed<span class="plus">+</span></div>
<div class="btn" style="left:519px;top:3530px;width:162px;height:48px">View More <svg viewBox="0 0 24 24"><circle cx="12" cy="12" r="11" fill="#fff"/><path d="m10 7 5 5-5 5" fill="none" stroke="#0054AA" stroke-width="3"/></svg></div>

<!-- FOOTER -->
<footer class="abs footer" role="img" aria-label="Faint photo of trucks on a highway under a blue overlay"></footer>
<div class="abs brand" style="left:145px;top:3808px;font-size:26px;line-height:28px">Brightlane<br><span style="font-size:18px;letter-spacing:6px">Rapid Rinse</span></div>
<div class="social" style="left:154px"></div>
<div class="social" style="left:195px"></div>
<div class="social" style="left:236px"></div>
<div class="social" style="left:276px"></div>
<div class="social" style="left:316px"></div>

<div class="abs foot-head" style="left:432px;top:3808px">Quick Links</div>
<div class="abs foot-list" style="left:433px;top:3846px">Home<br>About us<br>Our Services<br>News<br>Contact Us</div>
<div class="abs foot-head" style="left:613px;top:3808px">About Company</div>
<div class="abs foot-list" style="left:613px;top:3846px">Legal Information<br>Terms &amp; Condition<br>Privacy Policy<br>Support<br>Site Map</div>
<div class="abs foot-head" style="left:843px;top:3808px">Contact Us</div>

<svg class="abs" style="left:855px;top:3845px" width="14" height="14" viewBox="0 0 24 24"><path fill="#fff" d="M6.6 10.8a15 15 0 0 0 6.6 6.6l2.2-2.2c.3-.3.7-.4 1-.2 1.1.4 2.3.6 3.6.6.6 0 1 .4 1 1V20c0 .6-.4 1-1 1A17 17 0 0 1 3 4c0-.6.4-1 1-1h3.5c.6 0 1 .4 1 1 0 1.3.2 2.5.6 3.6.1.3 0 .7-.2 1z"/></svg>
<div class="abs contact-label" style="left:878px;top:3846px">Phone</div>
<div class="abs contact-val" style="left:880px;top:3870px">+1 (888) 888-8888</div>
<svg class="abs" style="left:853px;top:3906px" width="16" height="12" viewBox="0 0 16 12"><rect width="16" height="12" rx="1" fill="#fff"/><path d="m1 1 7 6 7-6" fill="none" stroke="#0054AA" stroke-width="1.5"/></svg>
<div class="abs contact-label" style="left:880px;top:3903px">Email</div>
<div class="abs contact-val" style="left:880px;top:3926px">info@companyname.com</div>
<svg class="abs" style="left:856px;top:3957px" width="12" height="16" viewBox="0 0 12 16"><path d="M6 0a6 6 0 0 0-6 6c0 4.5 6 10 6 10s6-5.5 6-10a6 6 0 0 0-6-6z" fill="#fff"/><circle cx="6" cy="6" r="2.2" fill="#0054AA"/></svg>
<div class="abs contact-label" style="left:878px;top:3957px">Location</div>
<div class="abs contact-val" style="left:880px;top:3980px;width:230px">123, Lorem ipsum dolor sit amet, consectetur adipiscing</div>

<div class="abs" style="left:0;top:4042px;width:1200px;height:1px;background:rgba(255,255,255,.35)"></div>
<div class="abs" style="left:1111px;top:4024px;width:36px;height:36px;border-radius:50%;background:var(--blue-mid);display:flex;align-items:center;justify-content:center"><svg width="14" height="14" viewBox="0 0 24 24"><path d="m5 15 7-7 7 7" fill="none" stroke="#fff" stroke-width="3"/></svg></div>
<div class="abs" style="left:0;top:4075px;width:1200px;text-align:center;font-size:14px;color:var(--white)">2024 Copyrights Company name &nbsp;| All Rights Reserved</div>

</body>
</html>
```